Marcus Delbridge Finance

Need a personal website advertising Equipment Finance,Business Finance,Commercial Finance, Construction Finance, Bridging Finance. Similar websites are www.corvalend.com.au / www.tarmivest.com.au / www.qbr7.com.au /wwwhalvecredit.com.au

Target Market(s)

Business People

Industry/Entity Type

Business

Number of Pages Required

3 page

Font styles to use
Serif
Sans Serif

Requirements
Must have
• All i want is a simple corporate looking website advertising Equipment Finance, Commercial Finance, Construction Finance, Business Finance, Bridging Finance,

```html
<!DOCTYPE html>
<html lang="en">
<head>
<meta charset="utf-8">
<title>Marcus Delbridge Finance</title>
<link rel="stylesheet" href="https://fonts.googleapis.com/css2?family=Open+Sans:wght@400;600;700&family=Raleway:wght@400;500;700&display=swap">
<style>
:root{
  --blue:#27a9e1;
  --green:#adc122;
  --green-dark:#9bae1a;
  --grey-bar:#ececec;
  --grey-band:#ebebeb;
  --text:#333;
  --muted:#666;
  --field:#f3f3f3;
  --field-line:#cfcfcf;
  --white:#fff;
}
*{box-sizing:border-box;margin:0;padding:0}
html,body{width:1200px;height:2456px;overflow:hidden;background:var(--white)}
body{position:relative;font-family:"Open Sans",Arial,sans-serif;color:var(--text)}
.abs{position:absolute}
.btn{position:absolute;display:flex;align-items:center;justify-content:center;gap:8px;background:var(--green);color:var(--white);font-weight:700;font-size:21px;letter-spacing:.3px;border-radius:3px}
.btn svg{width:14px;height:14px}

/* top bar */
.topbar{left:0;top:0;width:1200px;height:43px;background:var(--grey-bar);border-bottom:1px solid #ddd}
.topbar-phone{right:80px;top:6px;display:flex;align-items:center;gap:12px;color:var(--blue);font-weight:700;font-size:22px}

/* header */
.site-header{left:0;top:43px;width:1200px;height:106px;background:var(--white)}
.brand{left:80px;top:14px;color:var(--blue);font-family:"Open Sans",Arial,sans-serif;font-weight:400;line-height:1}
.brand-name{font-size:36px;display:block}
.brand-sub{font-size:22px;letter-spacing:12px;display:block;margin-top:8px}
.main-nav{right:80px;top:38px;display:flex;gap:46px;font-family:"Raleway",Arial,sans-serif;font-size:21px;color:#555}
.main-nav .active{color:var(--green)}

/* hero */
.hero{left:0;top:149px;width:1200px;height:573px;overflow:hidden}
.hero-photo{position:absolute;inset:0;background:linear-gradient(90deg,#f6f8fa 0%,#e9eef3 30%,#c9d4de 55%,#a9b4c0 75%,#d8e0e7 100%)}
.hero-title{left:80px;top:150px;font-family:"Raleway",Arial,sans-serif;font-weight:700;color:var(--blue);font-size:41px;line-height:52px}
.hero-text{left:80px;top:256px;width:520px;font-size:21px;line-height:32px;color:#222}
.hero-cta{left:77px;top:344px;width:210px;height:57px}

/* blue band */
.cta-band{left:0;top:722px;width:1200px;height:124px;background:var(--blue)}
.cta-band-text{left:80px;top:30px;font-family:"Raleway",Arial,sans-serif;font-size:46px;color:var(--white)}
.cta-band-btn{left:918px;top:33px;width:206px;height:57px}

/* welcome */
.section-title{left:0;width:1200px;text-align:center;font-family:"Raleway",Arial,sans-serif;font-weight:400;font-size:42px;color:var(--green)}
.section-title .hl{color:var(--blue)}
.section-text{left:120px;width:960px;text-align:center;font-size:15.5px;line-height:25px;color:var(--muted)}
.welcome-title{top:895px}
.welcome-text{top:958px}
.welcome-btn{left:514px;top:1056px;width:172px;height:57px}

/* services */
.services{left:0;top:1175px;width:1200px;height:488px;background:var(--grey-band)}
.services-title{top:48px}
.services-text{left:200px;width:800px;top:107px}
.service{top:180px;width:188px;text-align:center}
.service-photo{width:188px;height:135px}
.service-name{margin-top:10px;font-family:"Raleway",Arial,sans-serif;font-size:21px;color:var(--blue)}
.service-text{margin-top:4px;font-size:15.5px;line-height:25px;color:var(--muted)}

/* quote form */
.quote-title{top:1710px}
.field{position:absolute;background:var(--field);border:1px solid var(--field-line);border-radius:3px;font-size:15.5px;color:#666;padding:12px 10px}
.submit-btn{left:535px;top:1991px;width:130px;height:57px}

/* footer */
.site-footer{left:0;top:2110px;width:1200px;height:346px;background:var(--green);color:var(--white)}
.footer-brand{left:80px;top:62px;color:var(--white);line-height:1}
.footer-brand .brand-name{font-size:31px}
.footer-brand .brand-sub{font-size:19px;letter-spacing:11px;margin-top:4px}
.footer-col{top:2px}
.footer-head{font-family:"Raleway",Arial,sans-serif;font-size:27px;font-weight:400;margin-top:32px;margin-bottom:12px}
.footer-text{font-size:15.5px;line-height:25px}
.news-item{width:232px}
.news-date{display:flex;align-items:center;gap:6px;font-size:14.5px}
.news-rule{width:232px;height:1px;background:rgba(255,255,255,.85);margin:8px 0 12px}
.contact-row{display:flex;gap:12px;align-items:flex-start;font-size:15.5px;line-height:25px;margin-bottom:8px}
.contact-row svg{flex:none;margin-top:4px}
.socials{display:flex;gap:16px;margin-top:6px}
.social{width:46px;height:46px;border-radius:50%;border:2px solid var(--white)}
.social.filled{background:var(--white)}
.news-input{width:236px;height:42px;background:#c8d65b;font-size:15.5px;color:#fff;padding:10px 10px;margin-top:14px}
.subscribe{display:inline-flex;align-items:center;justify-content:center;width:162px;height:51px;background:var(--blue);font-family:"Raleway",Arial,sans-serif;font-size:21px;margin-top:22px;border-radius:2px}
.footer-rule{left:80px;top:291px;width:1040px;height:1px;background:rgba(255,255,255,.45)}
.copyright{left:0;top:307px;width:1200px;text-align:center;font-size:15.5px}
.copyright strong{color:#333}
</style>
</head>
<body>

<div class="abs topbar">
  <div class="abs topbar-phone">
    <svg width="24" height="24" viewBox="0 0 24 24"><path fill="#222" d="M6.6 10.8a15.1 15.1 0 0 0 6.6 6.6l2.2-2.2c.3-.3.7-.4 1-.2 1.1.4 2.3.6 3.6.6.6 0 1 .4 1 1V20c0 .6-.4 1-1 1C10.6 21 3 13.4 3 4c0-.6.4-1 1-1h3.5c.6 0 1 .4 1 1 0 1.3.2 2.5.6 3.6.1.3 0 .7-.2 1z"/></svg>
    123 555 0142
  </div>
</div>

<header class="abs site-header">
  <div class="abs brand"><span class="brand-name">Marcus Delbridge</span><span class="brand-sub">Finance</span></div>
  <nav class="abs main-nav"><span class="active">HOME</span><span>ABOUT</span><span>SERVICES</span><span>CONTACT</span></nav>
</header>

<section class="abs hero">
  <div class="hero-photo" role="img" aria-label="Photo of two businesswomen in grey suits in a bright office, one holding a clipboard"></div>
  <h1 class="abs hero-title">LOREM IPSUM IS SIMPLY<br>DUMMY TEXT.</h1>
  <p class="abs hero-text">Lorem Ipsum is simply dummy text of the printing and typesetting industry.</p>
  <div class="btn hero-cta">GET A QUOTE <svg viewBox="0 0 14 14"><path fill="#fff" d="M1 5.5h7V2l5 5-5 5V8.5H1z"/></svg></div>
</section>

<section class="abs cta-band">
  <p class="abs cta-band-text">Lorem Ipsum is simply dummy text.</p>
  <div class="btn cta-band-btn">CONTACT US <svg viewBox="0 0 14 14"><path fill="#fff" d="M1 5.5h7V2l5 5-5 5V8.5H1z"/></svg></div>
</section>

<h2 class="abs section-title welcome-title">WELCOME TO <span class="hl">MARCUS DELBRIDGE FINANCE</span></h2>
<p class="abs section-text welcome-text">Lorem Ipsum is dummy text of the printing and typesetting industry. Lorem Ipsum has been the industry's standard dummy text ever since the 1500s, when an unknown printer took a galley of type it to make a type specimen book. It has survived not only five centuries, but also the leap into electronic typesetting, remaining essentially unchanged.</p>
<div class="btn welcome-btn">READ MORE</div>

<section class="abs services">
  <h2 class="abs section-title services-title">SERVICES <span class="hl">WE PROVIDE</span></h2>
  <p class="abs section-text services-text">Lorem Ipsum is dummy text of the printing and typesetting industry. Lorem Ipsum has been the industry's standard dummy text ever since the 1500.</p>
  <div class="abs service" style="left:77px">
    <div class="service-photo" role="img" aria-label="Laptop beside printed financial charts" style="background:linear-gradient(135deg,#e8eef3,#9ccfe6 60%,#3a95c8)"></div>
    <div class="service-name">Equipment</div>
    <div class="service-text">Lorem Ipsum is dummy text of the printing and typesetting industry.</div>
  </div>
  <div class="abs service" style="left:291px">
    <div class="service-photo" role="img" aria-label="Businessman touching a glowing bar chart" style="background:linear-gradient(135deg,#5a5f66,#8e9aa6 50%,#3d6d99)"></div>
    <div class="service-name">Business</div>
    <div class="service-text">Lorem Ipsum is dummy text of the printing and typesetting industry.</div>
  </div>
  <div class="abs service" style="left:506px">
    <div class="service-photo" role="img" aria-label="Hands typing on a laptop and calculator" style="background:linear-gradient(135deg,#f2f2f2,#c9c9c9 60%,#8a8a8a)"></div>
    <div class="service-name">Commercial</div>
    <div class="service-text">Lorem Ipsum is dummy text of the printing and typesetting industry.</div>
  </div>
  <div class="abs service" style="left:720px">
    <div class="service-photo" role="img" aria-label="Glass office towers seen from below" style="background:linear-gradient(160deg,#9fc6e6,#2b5f9a 55%,#0f2f5c)"></div>
    <div class="service-name">Construction</div>
    <div class="service-text">Lorem Ipsum is dummy text of the printing and typesetting industry.</div>
  </div>
  <div class="abs service" style="left:935px">
    <div class="service-photo" role="img" aria-label="Modern arched bridge over a road at dusk" style="background:linear-gradient(160deg,#3f6f9a,#8fb3cf 55%,#264a6e)"></div>
    <div class="service-name">Bridging</div>
    <div class="service-text">Lorem Ipsum is dummy text of the printing and typesetting industry.</div>
  </div>
</section>

<h2 class="abs section-title quote-title">GET A <span class="hl">FREE QUOTE</span></h2>
<div class="field" style="left:188px;top:1788px;width:365px;height:46px">Enter name</div>
<div class="field" style="left:188px;top:1855px;width:365px;height:47px">Enter Email</div>
<div class="field" style="left:188px;top:1923px;width:365px;height:47px">Enter Contact No.</div>
<div class="field" style="left:573px;top:1788px;width:439px;height:182px">Enter message</div>
<div class="btn submit-btn">SUBMIT</div>

<footer class="abs site-footer">
  <div class="abs footer-brand"><span class="brand-name">Marcus Delbridge</span><span class="brand-sub">Finance</span>
    <p class="footer-text" style="margin-top:18px;width:230px;line-height:25px">Lorem Ipsum is dummy text of the printing and typesetting industry.</p>
  </div>

  <div class="abs footer-col" style="left:350px">
    <h3 class="footer-head">Latest News</h3>
    <div class="news-item footer-text">Lorem Ipsum is dummy text of the printing and typesetting.</div>
    <div class="news-date"><svg width="12" height="12" viewBox="0 0 12 12"><rect x="1" y="2" width="10" height="9" fill="none" stroke="#fff" stroke-width="1.4"/><path d="M1 5h10M4 1v2M8 1v2" stroke="#fff" stroke-width="1.4"/></svg>09 January 2017</div>
    <div class="news-rule"></div>
    <div class="news-item footer-text">Lorem Ipsum is dummy text of the printing and typesetting.</div>
    <div class="news-date"><svg width="12" height="12" viewBox="0 0 12 12"><rect x="1" y="2" width="10" height="9" fill="none" stroke="#fff" stroke-width="1.4"/><path d="M1 5h10M4 1v2M8 1v2" stroke="#fff" stroke-width="1.4"/></svg>09 January 2017</div>
  </div>

  <div class="abs footer-col" style="left:622px">
    <h3 class="footer-head">Get In Touch</h3>
    <div class="contact-row" style="width:240px"><svg width="14" height="18" viewBox="0 0 14 18"><path fill="#fff" d="M7 0a7 7 0 0 0-7 7c0 5 7 11 7 11s7-6 7-11a7 7 0 0 0-7-7zm0 9.5A2.5 2.5 0 1 1 7 4.5a2.5 2.5 0 0 1 0 5z"/></svg><span>Lorem Ipsum is simply dummy text of the printing.</span></div>
    <div class="contact-row" style="font-weight:700"><svg width="18" height="18" viewBox="0 0 24 24"><path fill="#fff" d="M6.6 10.8a15.1 15.1 0 0 0 6.6 6.6l2.2-2.2c.3-.3.7-.4 1-.2 1.1.4 2.3.6 3.6.6.6 0 1 .4 1 1V20c0 .6-.4 1-1 1C10.6 21 3 13.4 3 4c0-.6.4-1 1-1h3.5c.6 0 1 .4 1 1 0 1.3.2 2.5.6 3.6.1.3 0 .7-.2 1z"/></svg><span>123 555 0142</span></div>
    <div class="contact-row"><svg width="18" height="14" viewBox="0 0 18 14"><rect x="1" y="1" width="16" height="12" fill="none" stroke="#fff" stroke-width="1.5"/><path d="M1 1l8 7 8-7" fill="none" stroke="#fff" stroke-width="1.5"/></svg><span>info@marcusdelbridge.com</span></div>
    <div class="socials"><span class="social filled"></span><span class="social"></span><span class="social"></span></div>
  </div>

  <div class="abs footer-col" style="left:890px">
    <h3 class="footer-head">Newsletter</h3>
    <p class="footer-text" style="width:210px">Subscribe to stay on Marcus Delbridge.</p>
    <div class="news-input">Enter email id here...</div>
    <div class="subscribe">SUBSCRIBE</div>
  </div>

  <div class="abs footer-rule"></div>
  <p class="abs copyright">© <strong>Marcus Delbridge</strong> - 2017. All Rights Reserved.</p>
</footer>

</body>
</html>
```